Largest women's organization in New Hampshire needs a new graphic for their Facebook, Twitter and LI

Our organization is celebrating its 10th anniversary and we are the largest organization in New Hampshire for personal and professional development, businesses resources, networking and fun. Our "vibe" is one of community, fun, polished professionalism, feminity and lots of motivation and inspiration. We like quotes like "she believed she could so she did" and "stimulate your mind, nurture your soul" which is kind of our tag line. Our colors are pink, black, white and lime green. We host a lot of events with the biggest being the NH Larkridge Summit Days. Our website is www.larkridgeforum.com / https://www.frendlio.com/LarkridgeCircleForum/?ref=bookmarks

```html
<!DOCTYPE html>
<html lang="en">
<head>
<meta charset="utf-8">
<title>Larkridge Circle – Celebrating 10 Years</title>
<link href="https://fonts.googleapis.com/css2?family=Arimo:wght@400;700&display=swap" rel="stylesheet">
<style>
  :root {
    --pink: #e4418a;
    --black: #111111;
    --white: #ffffff;
    --band: rgba(40, 40, 44, 0.78);
    --curve-line: #6b6b70;
    --photo-warm: #7a3a3c;
    --photo-rose: #c9506a;
    --photo-dark: #3d2a2a;
    --photo-light: #c8a48e;
  }
  html, body {
    margin: 0;
    padding: 0;
    overflow: hidden;
    background: var(--white);
  }
  .cover {
    position: relative;
    width: 1200px;
    height: 444px;
    overflow: hidden;
    font-family: "Arimo", Arial, sans-serif;
    background: var(--white);
  }
  .event-photo {
    position: absolute;
    inset: 0;
    background:
      radial-gradient(ellipse at 55% 75%, var(--photo-rose) 0%, transparent 45%),
      radial-gradient(ellipse at 85% 30%, var(--photo-light) 0%, transparent 40%),
      linear-gradient(180deg, var(--photo-dark) 0%, var(--photo-warm) 55%, var(--photo-light) 100%);
  }
  .side-panel {
    position: absolute;
    inset: 0;
    width: 1200px;
    height: 444px;
  }
  .brand {
    position: absolute;
    left: 28px;
    top: 58px;
    display: flex;
    align-items: center;
    gap: 12px;
  }
  .brand-dot {
    width: 22px;
    height: 22px;
    border-radius: 50%;
    background: var(--pink);
  }
  .brand-name {
    font-size: 30px;
    font-weight: 700;
    color: var(--pink);
    line-height: 1.05;
  }
  .anniversary {
    position: absolute;
    left: 20px;
    top: 228px;
    color: var(--black);
  }
  .anniversary-label {
    font-size: 30px;
    line-height: 1;
  }
  .anniversary-number {
    font-size: 120px;
    font-weight: 400;
    color: var(--pink);
    line-height: 1;
    margin: 8px 0 4px -4px;
  }
  .anniversary-unit {
    font-size: 30px;
    line-height: 1;
  }
  .tagline-band {
    position: absolute;
    left: 134px;
    right: 0;
    bottom: 0;
    height: 63px;
    background: var(--band);
    display: flex;
    align-items: center;
    justify-content: center;
  }
  .tagline {
    margin: 0;
    padding-left: 40px;
    font-size: 29px;
    font-weight: 400;
    letter-spacing: 0.3px;
    color: var(--white);
    text-transform: uppercase;
  }
</style>
</head>
<body>
  <main class="cover">
    <div class="event-photo" role="img" aria-label="Group of smiling women seated at a round table during a conference luncheon, with attendees and banners in the background"></div>

    <svg class="side-panel" viewBox="0 0 1200 444" aria-hidden="true">
      <path d="M0 0 H305 C225 105 150 240 128 444 H0 Z" fill="#ffffff"/>
      <path d="M305 0 C225 105 150 240 128 444" fill="none" stroke="#6b6b70" stroke-width="3"/>
    </svg>

    <div class="tagline-band">
      <p class="tagline">Stimulate your mind, nurture your soul</p>
    </div>

    <div class="brand">
      <span class="brand-dot"></span>
      <span class="brand-name">Larkridge<br>Circle</span>
    </div>

    <div class="anniversary">
      <div class="anniversary-label">Celebrating</div>
      <div class="anniversary-number">10</div>
      <div class="anniversary-unit">Years</div>
    </div>
  </main>
</body>
</html>
```